OBK Farcoast Logistics Limited

We need the buissnes card to be very exclusive. As we are all young in our company. We need this to be the gate to make our clients feel deep interest for us.

We are focused in as International Trade advisors, and our products go from Oil Tanker Ships to Rubber balls for dogs.

Our Slogan is Reaching Far Shores.
And our main marketing will be through Internet.

We were stablished in 2009 In Mexico and we also have offices in Hong Kong.
We have representatives in China and Europe.

Target Market(s)

Is every company or Individual that wants to develop an International Project or product development or Logistic service of Goods and people.
Some of our current projects are Ship Brokerage, Mine Brokerage, Real State and Product Pormotional development.

Industry/Entity Type

It Company

Requirements
Must have
• Our Logo and slogan, and make the card accoriding to the logo.
Nice to have
• Our Colors

```html
<!DOCTYPE html>
<html lang="en">
<head>
<meta charset="utf-8">
<title>OBK Farcoast Logistics Limited – Business Card</title>
<link rel="stylesheet" href="https://fonts.googleapis.com/css2?family=Open+Sans:wght@400;600;700&display=swap">
<style>
  :root {
    --stage: #e9e6e1;
    --card: #231f20;
    --green: #8cc63f;
    --blue: #1ba1dc;
    --white: #ffffff;
    --ink: #1a1a1a;
  }
  * { box-sizing: border-box; margin: 0; padding: 0; }
  html, body {
    width: 1200px; height: 720px; overflow: hidden;
    background: var(--stage);
    font-family: "Open Sans", Arial, sans-serif;
  }
  .stage {
    position: relative; width: 1200px; height: 720px;
    display: flex; align-items: center; justify-content: center; gap: 40px;
  }
  .card {
    position: relative; width: 540px; height: 310px;
    background: var(--card); overflow: hidden;
    box-shadow: 0 6px 18px rgba(0,0,0,.25);
  }
  /* Contact side */
  .card-waves { position: absolute; inset: 0; width: 100%; height: 100%; }
  .brand {
    position: absolute; left: 52px; top: 62px; width: 170px;
    display: flex; flex-direction: column; align-items: center;
  }
  .brand-row { display: flex; align-items: center; gap: 12px; }
  .brand-dot { width: 34px; height: 34px; border-radius: 50%; background: var(--blue); }
  .brand-name { color: var(--green); font-size: 50px; font-weight: 700; letter-spacing: 2px; line-height: 1; }
  .brand-slogan { color: var(--blue); font-size: 11px; margin-top: 6px; white-space: nowrap; }
  .divider {
    position: absolute; left: 250px; top: 34px; width: 2px; height: 120px;
    background: linear-gradient(to bottom, var(--white), rgba(255,255,255,0));
  }
  .person { position: absolute; left: 268px; top: 26px; }
  .person-name { color: var(--green); font-size: 17px; font-weight: 700; }
  .person-role { color: var(--blue); font-size: 11px; margin-top: -2px; }
  .contacts {
    position: absolute; left: 276px; top: 72px; list-style: none;
    color: var(--white); font-size: 11.5px; line-height: 1.55;
  }
  .contacts li { display: flex; align-items: center; gap: 8px; }
  .contacts svg { width: 11px; height: 11px; fill: var(--white); flex: none; }
  .contacts .address { padding-left: 19px; margin-top: 4px; line-height: 1.3; }
  .web-front {
    position: absolute; right: 22px; top: 206px;
    color: var(--ink); font-size: 12px; font-weight: 700; letter-spacing: 1px;
    transform: rotate(-5deg);
  }
  /* Brand side */
  .card-back { display: flex; flex-direction: column; align-items: center; justify-content: center; }
  .back-brand { display: flex; align-items: center; gap: 22px; margin-top: -20px; }
  .back-dot { width: 90px; height: 90px; border-radius: 50%; background: var(--blue); }
  .back-name { color: var(--green); font-size: 96px; font-weight: 700; letter-spacing: 4px; line-height: 1; }
  .web-back {
    position: absolute; bottom: 46px; left: 0; right: 0; text-align: center;
    color: var(--white); font-size: 15px; letter-spacing: 4px;
  }
  .web-back .web-domain { color: var(--blue); }
</style>
</head>
<body>
<main class="stage">
  <section class="card card-front" aria-label="Business card, contact side">
    <svg class="card-waves" viewBox="0 0 540 310" aria-hidden="true">
      <path d="M0,246 C150,258 300,182 540,160 L540,170 C300,194 150,270 0,258 Z" fill="var(--blue)"/>
      <path d="M0,260 C150,272 300,196 540,174 L540,176 C300,199 150,275 0,263 Z" fill="var(--white)" opacity=".8"/>
      <path d="M0,265 C150,277 300,201 540,179 L540,244 C360,250 200,288 0,294 Z" fill="var(--green)"/>
      <path d="M0,294 C200,288 360,250 540,244 L540,250 C360,258 200,296 0,304 Z" fill="var(--blue)"/>
    </svg>
    <div class="brand">
      <div class="brand-row">
        <span class="brand-dot"></span>
        <span class="brand-name">OBK</span>
      </div>
      <p class="brand-slogan">Reaching Far Shores</p>
    </div>
    <div class="divider"></div>
    <div class="person">
      <p class="person-name">Your Name</p>
      <p class="person-role">Position</p>
    </div>
    <ul class="contacts">
      <li><svg viewBox="0 0 24 24"><path d="M6.6 10.8a15 15 0 0 0 6.6 6.6l2.2-2.2a1 1 0 0 1 1-.25 11.4 11.4 0 0 0 3.6.57 1 1 0 0 1 1 1V20a1 1 0 0 1-1 1A17 17 0 0 1 3 4a1 1 0 0 1 1-1h3.5a1 1 0 0 1 1 1c0 1.25.2 2.45.57 3.570a1 1 0 0 1-.25 1z"/></svg>123-456-7890</li>
      <li><svg viewBox="0 0 24 24"><path d="M7 1h10a2 2 0 0 1 2 2v18a2 2 0 0 1-2 2H7a2 2 0 0 1-2-2V3a2 2 0 0 1 2-2zm0 3v14h10V4zm5 15.5a1.2 1.2 0 1 0 0 2.4 1.2 1.2 0 0 0 0-2.4z"/></svg>123-456-7890</li>
      <li><svg viewBox="0 0 24 24"><path d="M2 5h20v14H2zm2 2v.5l8 5 8-5V7zm0 2.8V17h16V9.8l-8 5z"/></svg>info@farcoast.com</li>
      <li class="address">00, Complex Name<br>City, State, 00045</li>
    </ul>
    <p class="web-front">www.farcoast.com</p>
  </section>

  <section class="card card-back" aria-label="Business card, brand side">
    <div class="back-brand">
      <span class="back-dot"></span>
      <span class="back-name">OBK</span>
    </div>
    <p class="web-back">www.<span class="web-domain">farcoast</span>.com</p>
  </section>
</main>
</body>
</html>
```